Briloran Clear Springs needs a new business card design (we produce and sell pure bottled water)

We need a clean modern design for our new business cards, We have an existing logo which ultimately cannot be changed, however it could be slighty improved and the colours adjusted. We have this existing logo on all of our bottles, vehicles etc.

Our company slogan is "Pure down to the last drop".
Along with our relevant company information
(Address, phone, website email etc) we will only be using names and not putting position titles for flexibilty.

We are looking for a clean, minimalist modern design.

You can view our website (if need of an update also!) to see our business.

Industry/Entity Type

Business

Contact Information for Business Card

Staff Name : XXXXXX XXXXXX
Address : 9/41 Tavenor St
Halden Rise QLD 4172
Staff Mobile Number : 04XX XXX XXX
Office Phone Number : 07 3918 2457
Staff Email Address : XXXX@brilorancleargo.com.au
Website : www.brilorancleargo.com.au

Font styles to use
Sans Serif

Colors
cee9f5
33a6d7
0492cd
0455a3
3276b5
85abd2
cedeed

Requirements
Must have
• The ability to edit and change the staff members details as we will need to edit for each respective staff member (7 in total)

```html
<!DOCTYPE html>
<html lang="en">
<head>
<meta charset="UTF-8">
<title>Briloran Clear Springs – Business Card</title>
<link href="https://fonts.googleapis.com/css2?family=Source+Sans+3:wght@400;600;800&display=swap" rel="stylesheet">
<style>
  :root {
    --brand-navy: #0455a3;
    --brand-sky: #0492cd;
    --brand-ice: #cee9f5;
    --brand-mist: #85abd2;
    --card-white: #ffffff;
    --stage: #e9edf1;
  }
  * { margin: 0; padding: 0; box-sizing: border-box; }
  html, body {
    width: 1200px; height: 900px; overflow: hidden;
    background: var(--stage);
    font-family: "Source Sans 3", sans-serif;
  }
  .canvas { position: relative; width: 1200px; height: 900px; }

  .card { position: absolute; width: 556px; height: 343px; box-shadow: 0 6px 20px rgba(0,0,0,.15); }

  /* Front */
  .card-front { left: 238px; top: 62px; background: var(--card-white); }
  .staff-name {
    position: absolute; left: 31px; top: 78px;
    font-size: 20px; font-weight: 600; color: var(--brand-sky);
  }
  .info-band {
    position: absolute; left: 0; top: 140px; width: 502px; height: 169px;
    background: var(--brand-navy); color: var(--card-white);
  }
  .address { position: absolute; left: 31px; top: 20px; font-size: 15.5px; line-height: 20px; }
  .contact-list { position: absolute; left: 31px; top: 74px; list-style: none; font-size: 15.5px; line-height: 20.5px; }
  .contact-list li { display: flex; align-items: center; gap: 9px; }
  .contact-list svg { width: 11px; height: 11px; fill: none; stroke: var(--brand-mist); stroke-width: 1.6; }
  .front-brand {
    position: absolute; right: 22px; bottom: 14px; width: 150px;
    text-align: right; font-size: 21px; font-weight: 800; line-height: 21px;
    color: var(--card-white); text-transform: uppercase;
  }

  /* Back */
  .card-back { left: 457px; top: 518px; width: 560px; background: var(--brand-navy); }
  .back-brand {
    position: absolute; left: 188px; top: 190px;
    display: flex; align-items: center; gap: 12px;
  }
  .back-brand .dot { width: 22px; height: 22px; border-radius: 50%; background: var(--card-white); }
  .back-brand span {
    font-size: 30px; font-weight: 800; line-height: 28px;
    color: var(--card-white); text-transform: uppercase;
  }
</style>
</head>
<body>
<main class="canvas">

  <section class="card card-front" aria-label="Business card front">
    <h1 class="staff-name">Marcus Ellery</h1>
    <div class="info-band">
      <p class="address">9/41 Tavenor St<br>Halden Rise QLD 4172</p>
      <ul class="contact-list">
        <li><svg viewBox="0 0 12 12"><rect x="3" y="1" width="6" height="10" rx="1"/></svg>0400 581 273</li>
        <li><svg viewBox="0 0 12 12"><path d="M2 1.5l2.5 0 1 2.5-1.5 1a6 6 0 0 0 3 3l1-1.5 2.5 1v2.5c-5 0-8.5-3.5-8.5-8.5z"/></svg>07 3918 2457</li>
        <li><svg viewBox="0 0 12 12"><rect x="1" y="2.5" width="10" height="7"/><path d="M1 2.5l5 4 5-4"/></svg>info@brilorancleargo.com.au</li>
        <li><svg viewBox="0 0 12 12"><circle cx="6" cy="6" r="4.8"/><path d="M1.2 6h9.6M6 1.2c2.4 2.6 2.4 7 0 9.6M6 1.2c-2.4 2.6-2.4 7 0 9.6"/></svg>www.brilorancleargo.com.au</li>
      </ul>
      <p class="front-brand">Briloran Clear Springs</p>
    </div>
  </section>

  <section class="card card-back" aria-label="Business card back">
    <div class="back-brand">
      <div class="dot"></div>
      <span>Briloran<br>Clear Springs</span>
    </div>
  </section>

</main>
</body>
</html>
```